Salon and Spa Distributor Business Card

Need a business card. We are are distributor in the salon and spa industry. We identify with natural beauty. Need a card with:
Company Name: Petal Quarry"
Title: "President & CEO"
Address
Company Phone number
email
website
Tag Line:" The Professional Salon Source"

Industry/Entity Type

Business

Contact Information for Business Card

Name: Dov Strommen
Title: "President & CEO"
Address: 31 Harlow Ln, Bexmoor, NJ 07813
Company Phone number: 800-463-5918
email: dovstrommen@petalquarry.example
website: www.petalquarry.example

Requirements
Should not have
• No black backgrounds

```html
<!DOCTYPE html>
<html lang="en">
<head>
<meta charset="utf-8">
<title>Petal Quarry – Business Card</title>
<link rel="stylesheet" href="https://fonts.googleapis.com/css2?family=Questrial&display=swap">
<style>
  :root {
    --page-bg: #e9ebe8;
    --card-front: #1e4a2c;
    --card-front-edge: #163a22;
    --card-light: #ffffff;
    --green-pale: #a6e08a;
    --green-light: #6cc24a;
    --green-mid: #3fa63a;
    --green-deep: #137a2e;
    --ink: #1c1c1c;
    --white: #ffffff;
    --font-main: "Questrial", "Century Gothic", sans-serif;
  }
  * { box-sizing: border-box; margin: 0; padding: 0; }
  html, body { width: 1200px; height: 880px; overflow: hidden; }
  body {
    background: var(--page-bg);
    font-family: var(--font-main);
    position: relative;
  }
  .card {
    position: absolute;
    left: 280px;
    width: 640px;
    height: 366px;
    border-radius: 22px;
    overflow: hidden;
    box-shadow: 0 10px 28px rgba(0,0,0,0.18);
  }

  /* Front */
  .card--front {
    top: 56px;
    background: linear-gradient(160deg, var(--card-front), var(--card-front-edge));
  }
  .front-brand {
    position: absolute;
    left: 0; right: 0; top: 118px;
    display: flex;
    align-items: center;
    justify-content: center;
    gap: 22px;
  }
  .front-dot {
    width: 64px; height: 64px;
    border-radius: 50%;
    background: linear-gradient(160deg, var(--green-light), var(--green-deep));
    flex: none;
  }
  .front-name {
    font-size: 46px;
    color: var(--green-pale);
    letter-spacing: 0.5px;
    line-height: 1;
  }
  .front-tagline {
    position: absolute;
    left: 0; right: 0; top: 230px;
    text-align: center;
    font-size: 17px;
    letter-spacing: 4px;
    color: var(--white);
  }

  /* Back */
  .card--back { top: 458px; background: var(--card-light); }
  .back-circle {
    position: absolute;
    left: -70px; top: 70px;
    width: 360px; height: 360px;
    border-radius: 50%;
    background: linear-gradient(150deg, var(--green-light) 20%, var(--green-deep) 100%);
  }
  .back-info {
    position: absolute;
    left: 340px; top: 34px; right: 24px;
  }
  .brand-name {
    font-size: 40px;
    color: var(--green-mid);
    line-height: 1;
  }
  .brand-tagline {
    font-size: 15px;
    color: var(--ink);
    margin-top: 6px;
  }
  .person-name {
    font-size: 22px;
    color: var(--green-mid);
    margin-top: 28px;
    line-height: 1.1;
  }
  .person-title { font-size: 15px; color: var(--ink); }
  .address {
    font-size: 15px;
    color: var(--ink);
    margin-top: 14px;
    line-height: 1.35;
  }
  .contact-list { list-style: none; margin-top: 12px; }
  .contact-item {
    display: flex; align-items: center; gap: 8px;
    font-size: 14.5px; color: var(--ink);
    margin-bottom: 5px;
    white-space: nowrap;
  }
  .contact-icon {
    width: 18px; height: 18px; flex: none;
    border-radius: 4px;
    background: var(--green-mid);
    display: flex; align-items: center; justify-content: center;
  }
</style>
</head>
<body>
  <section class="card card--front">
    <div class="front-brand">
      <span class="front-dot"></span>
      <span class="front-name">Petal Quarry</span>
    </div>
    <div class="front-tagline">The Professional Salon Source</div>
  </section>

  <section class="card card--back">
    <div class="back-circle"></div>
    <div class="back-info">
      <div class="brand-name">Petal Quarry</div>
      <div class="brand-tagline">The Professional Salon Source</div>
      <div class="person-name">Dov Strommen</div>
      <div class="person-title">President &amp; CEO</div>
      <div class="address">31 Harlow Ln,<br>Bexmoor, NJ 07813</div>
      <ul class="contact-list">
        <li class="contact-item">
          <span class="contact-icon">
            <svg width="12" height="12" viewBox="0 0 12 12"><path d="M2.5 1.5h2l1 2.5-1.3 1a6 6 0 0 0 2.8 2.8l1-1.3 2.5 1v2a1 1 0 0 1-1 1A8.5 8.5 0 0 1 1.5 2.5a1 1 0 0 1 1-1z" fill="#fff"/></svg>
          </span>800-463-5918
        </li>
        <li class="contact-item">
          <span class="contact-icon">
            <svg width="12" height="12" viewBox="0 0 12 12"><rect x="1" y="2.5" width="10" height="7" rx="1" fill="none" stroke="#fff" stroke-width="1.2"/><path d="M1.5 3l4.5 3.5L10.5 3" fill="none" stroke="#fff" stroke-width="1.2"/></svg>
          </span>dovstrommen@petalquarry.example
        </li>
        <li class="contact-item">
          <span class="contact-icon">
            <svg width="12" height="12" viewBox="0 0 12 12"><circle cx="6" cy="6" r="4.6" fill="none" stroke="#fff" stroke-width="1.1"/><ellipse cx="6" cy="6" rx="2" ry="4.6" fill="none" stroke="#fff" stroke-width="1"/><path d="M1.4 6h9.2" stroke="#fff" stroke-width="1"/></svg>
          </span>www.petalquarry.example
        </li>
      </ul>
    </div>
  </section>
</body>
</html>
```